Packaging design - PROTEIN BALLS

PACKAGING
The packaging is a round carton roll, size: Ø73x180 mm, mockup sample enclosed, The label on the carton roll should have a size of 225x178 mm (width x height)

PRODUCT
Chrunchy, cheesy PROTEIN BALLS (100% pure cheese) with a huge amount of protein (65%), a lot of calcium and very low carbogydrates (3%). Diameter about 1.5 cm.

DESIGN
Since our customers are very sporty people, runner, bodybuilder, etc. The design must fit to this sporty customer segment.

FILES
We need the open data for InDesign with all fonts and pictures. If there are licenses tu buy, we will do it.

SUMMARY
1. SNACK
• Crunchy cheese balls with a diameter of about 1.5cm
• 3 different flavors: "Swiss Alpine Salt", "Provencale" and "Hot Chili"
• High in Protein (65%) and Calcium (2%)
• Low in carbohydrates (3%)

2. PACKAGING
• Carton roll, size: Ø73x180 mm
• Background can be every color, but we think a black one will be high premium.
• Maybe different sports are represented in the background, maybe also cheese
• Be creative
• Label applied, size: 225x178 mm

3. DESIGN
• Product name = (Cheese) PROTEIN BALLS
• 3 different colors for the 3 flavors "Swiss Alpine Salt", "Provencale" and "Hot Chili"
• HighProtein, High Calcium and LowCarb must be pointed out on the front
• Swissness: Swiss made must be pointed out
• fresh and young design, most customers are sporty people, pumper with a strong body awareness

Target Market(s)

TARGET CUSTOMER
Our main customers are extremely sporty people, who work very hard on their muscles and fitness, most of them are runners, cross fitnesser, bodybuilders, etc We will launch the product in fitness centers, in supplement shops and we are planning to make some stories with sporty influencer.

Font styles to use
Serif
Sans Serif

Requirements
Must have
• Cheese, naturalness, healthy, PROTEIN balls, muscles, Swissness must showed on the product.

```html
<!DOCTYPE html>
<html lang="en">
<head>
<meta charset="utf-8">
<title>Cheese Protein Balls – Label Range</title>
<link href="https://fonts.googleapis.com/css2?family=Bebas+Neue&family=Dancing+Script:wght@700&family=Amatic+SC:wght@700&display=swap" rel="stylesheet">
<style>
  :root{
    --page:#ffffff;
    --label:#3a3a3a;
    --label-dark:#2e2e2e;
    --label-edge:#454545;
    --figure:#4a4a4a;
    --ink:#f4f4f2;
    --cream:#d9ccaa;
    --swiss-red:#c8423b;
    --salt:#1a8fd0;
    --herb:#7f9f3e;
    --chili:#c23a33;
    --badge-white:#f2f2f2;
  }
  *{margin:0;padding:0;box-sizing:border-box}
  html,body{width:1200px;height:1200px;overflow:hidden;background:var(--page)}
  .range{position:relative;width:1200px;height:1200px}
  .label{
    position:absolute;top:200px;width:245px;height:700px;
    background:linear-gradient(90deg,var(--label-dark) 0%,var(--label) 18%,var(--label-edge) 55%,var(--label) 85%,var(--label-dark) 100%);
    overflow:hidden;
  }
  .label--salt{left:103px;--accent:var(--salt)}
  .label--herb{left:477px;--accent:var(--herb)}
  .label--chili{left:852px;--accent:var(--chili)}
  .label__footer{position:absolute;left:0;right:0;bottom:0;height:50px;background:rgba(0,0,0,.12)}
  .athletes-art{
    position:absolute;left:20px;top:70px;width:205px;height:330px;border-radius:40% 40% 10% 10%;
    background:radial-gradient(ellipse at 50% 45%,var(--figure) 0%,rgba(74,74,74,.4) 60%,rgba(74,74,74,0) 100%);
  }
  .origin{
    position:absolute;top:84px;left:0;right:0;display:flex;justify-content:center;align-items:center;gap:6px;
    font-family:"Bebas Neue",sans-serif;font-size:21px;letter-spacing:2px;color:var(--ink);
  }
  .origin svg{width:30px;height:26px}
  .product{position:absolute;top:205px;left:0;right:0;text-align:center}
  .product__kind{font-family:"Dancing Script",cursive;font-size:46px;color:var(--cream);line-height:1;margin-bottom:8px}
  .product__name{font-family:"Bebas Neue",sans-serif;font-size:78px;line-height:.9;color:var(--ink);letter-spacing:1px}
  .product__audience{margin-top:20px;font-family:"Bebas Neue",sans-serif;font-size:24px;letter-spacing:3px;color:var(--ink)}
  .flavour{
    position:absolute;z-index:2;top:488px;left:20px;width:190px;height:46px;background:var(--accent);
    display:flex;align-items:center;justify-content:center;
    font-family:"Dancing Script",cursive;font-size:25px;color:#fff;white-space:nowrap;
  }
  .flavour-art{position:absolute;z-index:1;top:515px;right:4px;width:34px;height:48px;border-radius:50%;opacity:.9}
  .label--salt .flavour-art{background:radial-gradient(circle,#e6e6e6,#9aa 90%)}
  .label--herb .flavour-art{background:radial-gradient(circle,#8aa860,#5c7a3a 90%)}
  .label--chili .flavour-art{background:radial-gradient(circle,#d84a3a,#8e231b 90%)}
  .claims{position:absolute;top:560px;left:0;right:0;display:flex;justify-content:center;gap:8px}
  .claim{
    width:56px;height:56px;border-radius:50%;border:2px solid #fff;
    display:flex;flex-direction:column;align-items:center;justify-content:center;
    font-family:"Amatic SC",sans-serif;font-weight:700;font-size:18px;line-height:.88;text-align:center;
    background:var(--badge-white);color:var(--accent);box-shadow:0 0 0 2px var(--label-dark);
  }
  .claim--primary{background:var(--accent);color:#fff}
</style>
</head>
<body>
<main class="range">

  <section class="label label--salt">
    <div class="athletes-art" role="img" aria-label="Faint silhouettes of athletes in the background"></div>
    <div class="origin">Swiss Made
      <svg viewBox="0 0 30 26" aria-hidden="true"><rect width="30" height="26" fill="var(--swiss-red)"/><rect x="12" y="6" width="6" height="14" fill="#fff"/><rect x="8" y="10" width="14" height="6" fill="#fff"/></svg>
    </div>
    <div class="product">
      <div class="product__kind">Cheese</div>
      <div class="product__name">Protein<br>Balls</div>
      <div class="product__audience">- For Athletes -</div>
    </div>
    <div class="flavour">Swiss Alpine Salt</div>
    <div class="flavour-art" role="img" aria-label="Drawing of a salt shaker"></div>
    <div class="claims">
      <div class="claim claim--primary">Low carb<br>3%</div>
      <div class="claim">High<br>protein<br>65%</div>
      <div class="claim">Calcium<br>2%</div>
    </div>
    <div class="label__footer"></div>
  </section>

  <section class="label label--herb">
    <div class="athletes-art" role="img" aria-label="Faint silhouettes of athletes in the background"></div>
    <div class="origin">Swiss Made
      <svg viewBox="0 0 30 26" aria-hidden="true"><rect width="30" height="26" fill="var(--swiss-red)"/><rect x="12" y="6" width="6" height="14" fill="#fff"/><rect x="8" y="10" width="14" height="6" fill="#fff"/></svg>
    </div>
    <div class="product">
      <div class="product__kind">Cheese</div>
      <div class="product__name">Protein<br>Balls</div>
      <div class="product__audience">- For Athletes -</div>
    </div>
    <div class="flavour">Provencale</div>
    <div class="flavour-art" role="img" aria-label="Drawing of basil leaves"></div>
    <div class="claims">
      <div class="claim claim--primary">Low carb<br>3%</div>
      <div class="claim">High<br>protein<br>65%</div>
      <div class="claim">Calcium<br>2%</div>
    </div>
    <div class="label__footer"></div>
  </section>

  <section class="label label--chili">
    <div class="athletes-art" role="img" aria-label="Faint silhouettes of athletes in the background"></div>
    <div class="origin">Swiss Made
      <svg viewBox="0 0 30 26" aria-hidden="true"><rect width="30" height="26" fill="var(--swiss-red)"/><rect x="12" y="6" width="6" height="14" fill="#fff"/><rect x="8" y="10" width="14" height="6" fill="#fff"/></svg>
    </div>
    <div class="product">
      <div class="product__kind">Cheese</div>
      <div class="product__name">Protein<br>Balls</div>
      <div class="product__audience">- For Athletes -</div>
    </div>
    <div class="flavour">Hot Chili</div>
    <div class="flavour-art" role="img" aria-label="Drawing of red chili peppers"></div>
    <div class="claims">
      <div class="claim claim--primary">Low carb<br>3%</div>
      <div class="claim">High<br>protein<br>65%</div>
      <div class="claim">Calcium<br>2%</div>
    </div>
    <div class="label__footer"></div>
  </section>

</main>
</body>
</html>
```